A unique communication angle to crowdfunding

Looking for a fresh redesign of a crowd funding website that deals in real estate. I already have the content, but am looking to take the design to the next level.

Existing real estate crowd funding sites focus on the real estate. I want to explore communication angle that:
- puts the investor in the centre of the communication: "become a baron"
- highlights the international nature (international properties, international investors)

There's also quite a lot of copy on the site, as we need to explain the service in quite a bit of detail. There's room to reduce the copy and replace with graphics. Could also consider clicking to see different text (see our difference section in http://galleonfairs.com)

The backend of the platform is already being worked on by a specialist crowd funding service provider.

In total there are 5 pages to be designed.

The homepage is really important. Right now it looks quite dated. It doesn't have a great layout. Note there is no mobile version of the website, so the pages need to be seen well on mobile devices. When looking at the brief, refer to the following links too:

current website:
http://pennyduke.com

some revisions made so far:
http://preview.stakeharbor.com/7K3LQ9

Attached are logo files and another file which contained copy for the pages. No need to rework the logo.

Please make sure to use the same copy in the brief on the webpages, to ensure the layouts work. Designers are free to propose images they feel work on the pages.

I would like to see if rather than tweaking the pages, it's possible to come up with a better design concept. If the 5 pages are accepted, there's a chance I'll request an additional 4 pages.
Updates

Please note the font used in the logo is called "harabara" in case you decide to use it in any of the titles, etc.

Please note there is one additional page for which we would like to review designs. Note the page would be a template to be used on all future real estate detail pages. Here is an example of the current design for reference:

http://pennyduke.com/projects/view/14

In total there are 5 page designs required, (homepage + 4)

Thank you

FYI -

Just a quick note to give information from similar UK real estate crowdfunding sites:
http://www.housewalrus.co.uk
http://tiderock.co.uk
https://www.fundquarry.com

Of the above, only tiderock has a nice clean looking landing page. Information is clear and well laid out.

Hi all, just uploaded a new file in the brief. Contains some comments and a website reference. I thought it may help to explain how we could convey international aspect as well as how we could convey images in a more modern way. This is an option you can consider, but its entirely up to you how how answer the brief. Thanks!

Reason: As requested by some designers needing more time to complete their work. Continue to share your work in progress and receive timely feedback before the deadline.

We would like to let you know that we have just shortlisted the best designs. Together with that, we have also passed some detailed feedback to all designers who weren't shortlisted. If we didn't contact you, please let us know. If you haven't submitted a design or are working on revisions, please note these will no longer be taken into account now. We hope you understand that we need to close the project today. Thank you all once again for your great work and design concepts. Here's hoping we meet again on a future design brief. Cheers, pennyduke team.

Target Market(s)

At the moment, only rich are able to buy real estate. With this service, anyone can become a landlord. Target buyers:

Young professionals, looking to diversify from stock market and lower risk
People nearing retirement, looking for stable rental incomes
Retirees - looking to supplement pensions with possibility of capital gains
Parents - looking for a way to save long term for their children (instead of low interest paying bank accounts)

Industry/Entity Type

Communication

Font styles to use
Sans Serif
Other font styles liked:
• harabara

Colors
add136
f5f9eb
959595
000000

Requirements
Must have
• Overall, the site must convey "whoever you are, you too can become a landlord", and that you don't need to be wealthy to invest in real estate. See

Communication should put the investor (or the baron) at the centre. The investor can be any of those described in the target market.

Show the aspirational side of property ownership.

In addition to the investor/baron character, the second main theme is international. No other real estate crowdfunding website highlights this.
Nice to have
• Banner could show different consumer types, to illustrate that the service can appeal to many different profiles. Refer to attached file "home page reference - plainasbread.com" as an example of how this could be done.

Aim to show the international side of the service. Properties around the world, investors around the world.

```html
<!DOCTYPE html>
<html lang="en">
<head>
<meta charset="utf-8">
<title>pennyduke – Become a property baron</title>
<link rel="stylesheet" href="https://fonts.googleapis.com/css2?family=Open+Sans:wght@300;400;600;700&display=swap">
<style>
:root{
  --green:#add136;
  --green-deep:#8fb521;
  --pale:#f5f9eb;
  --grey:#959595;
  --grey-dark:#6f6f6f;
  --ink:#000000;
  --text:#4a4a4a;
  --white:#ffffff;
  --blue:#1f7fc4;
  --footer-text:#8a8a8a;
}
*{box-sizing:border-box;margin:0;padding:0}
html,body{width:1200px;height:4000px;overflow:hidden}
body{font-family:"Open Sans",Arial,sans-serif;color:var(--text);background:var(--white);position:relative}

/* Hero */
.hero{position:relative;height:900px;overflow:hidden}
.hero-photo{position:absolute;inset:0;background:
  radial-gradient(ellipse at 62% 38%,#d9533a 0,#c8462f 6%,rgba(200,70,47,0) 16%),
  linear-gradient(180deg,#cfd6d8 0%,#b9b3a6 38%,#9a8470 62%,#5f5043 100%)}
.hero-shade{position:absolute;inset:0;background:linear-gradient(180deg,rgba(0,0,0,.05) 0%,rgba(0,0,0,0) 40%,rgba(0,0,0,.35) 100%)}
.topbar{position:absolute;top:0;left:0;right:0;height:80px;display:flex;align-items:center;padding:0 40px}
.brand{display:flex;align-items:center;gap:12px;color:var(--white);font-weight:700;font-size:30px}
.brand-dot{width:34px;height:34px;border-radius:50%;background:var(--green)}
.main-nav{display:flex;gap:22px;margin-left:40px}
.main-nav a{color:var(--white);text-decoration:none;font-size:15px;font-weight:600;letter-spacing:.3px}
.social{margin-left:auto;display:flex;gap:10px}
.social span{width:30px;height:30px;border:2px solid var(--white);border-radius:50%}
.hero-copy{position:absolute;top:585px;left:0;right:0;text-align:center;color:var(--white)}
.hero-copy .lead{font-size:30px;font-weight:300;letter-spacing:2px}
.hero-copy h1{font-size:34px;font-weight:700;letter-spacing:1.5px;margin-top:4px}
.scroll-btn{position:absolute;left:560px;top:725px;width:80px;height:80px;border:4px solid var(--white);border-radius:50%;display:flex;align-items:center;justify-content:center}
.slider-dots{position:absolute;top:850px;left:0;right:0;display:flex;justify-content:center;gap:10px}
.slider-dots span{width:14px;height:14px;border-radius:50%;background:rgba(255,255,255,.6)}
.slider-dots span.active{background:var(--white)}

/* Intro band */
.intro{height:250px;background:var(--green);text-align:center;color:var(--white);padding-top:28px}
.intro-icon{width:78px;height:78px;border:3px solid var(--white);border-radius:50%;margin:0 auto;display:flex;align-items:center;justify-content:center}
.intro h2{font-size:24px;font-weight:700;margin-top:14px}
.intro p{font-size:17px;line-height:23px;width:960px;margin:4px auto 0}

/* Actions */
.actions{height:315px;background:var(--pale);display:flex;padding:60px 0 0 95px;gap:0}
.action{display:flex;width:505px;gap:24px}
.action-tile{width:140px;height:140px;background:var(--grey);color:var(--white);display:flex;flex-direction:column;align-items:center;justify-content:center;font-size:13px;text-align:center;line-height:16px;text-transform:uppercase}
.action-tile svg{margin-bottom:10px}
.action h3{font-size:28px;font-weight:600;color:var(--grey-dark);margin-top:6px}
.action p{font-size:18px;line-height:24px;color:var(--grey);width:300px;margin-top:4px}

/* Projects */
.projects{height:575px;text-align:center;padding-top:42px}
.section-title{font-size:26px;font-weight:700;color:var(--green)}
.section-sub{font-size:18px;line-height:24px;color:var(--grey);width:760px;margin:6px auto 0}
.section-sub a{color:var(--green);text-decoration:none}
.cards{display:flex;gap:45px;justify-content:center;margin-top:30px}
.card{width:300px;height:375px;background:var(--white);box-shadow:0 0 0 1px #e3e3e3;text-align:left;position:relative}
.card-photo{height:140px;background:linear-gradient(180deg,#7ea0c2 0%,#4f6a88 55%,#2e3a48 100%)}
.card:nth-child(2) .card-photo{background:linear-gradient(180deg,#1d2c4a 0%,#32476d 55%,#12161f 100%)}
.card:nth-child(3) .card-photo{background:linear-gradient(180deg,#8eb4d6 0%,#6d87a2 55%,#394656 100%)}
.tag-new{position:absolute;top:12px;left:14px;background:var(--blue);color:var(--white);font-size:11px;padding:3px 8px}
.tag-price{position:absolute;top:0;right:0;background:var(--green);color:var(--white);font-size:15px;font-weight:700;padding:8px 14px}
.card-body{padding:12px 14px}
.card h4{font-size:16px;font-weight:700;color:#2f6f9a}
.card p{font-size:13px;line-height:17px;color:var(--text);margin-top:6px;height:70px}
.progress{height:14px;background:#eeeeee;margin-top:14px}
.progress i{display:block;height:100%;background:var(--green)}
.funded{font-size:13px;color:var(--text);margin-top:10px;padding-bottom:8px;border-bottom:1px solid #e6e6e6}
.card-link{font-size:13px;color:var(--green-deep);margin-top:8px;display:block;font-weight:600}

/* Community */
.community{height:1290px;text-align:center;padding-top:25px}
.bar-title{width:1000px;margin:0 auto;height:40px;background:var(--green);color:var(--white);font-size:18px;line-height:40px;border-radius:2px}
.community .bar-title.first{margin-top:28px}
.world-map{width:1040px;height:430px;margin:18px auto 0;background:radial-gradient(ellipse at 50% 50%,#b0b0b0 0,#c6c6c6 55%,#ffffff 75%)}
.legend{width:1000px;margin:24px auto 0;text-align:left}
.legend-row{display:flex;align-items:center;gap:16px;font-size:17px;color:var(--grey-dark);margin-bottom:14px}
.legend-row i{width:36px;height:36px;display:block;background:var(--green)}
.legend-row i.pink{background:#e2245f}
.community .bar-title.second{margin-top:50px}
.donut-wrap{position:relative;width:1000px;height:370px;margin:0 auto}
.donut-wrap svg{position:absolute;left:190px;top:16px}
.donut-label{position:absolute;left:600px;font-size:22px;color:var(--text)}
.donut-label.invested{top:60px}
.donut-label.pledged{top:220px}
.donut-center{position:absolute;left:190px;top:128px;width:340px;text-align:center;color:var(--green);font-weight:700}
.donut-center .cur{font-size:36px;line-height:44px;display:block}
.donut-center .amt{font-size:46px;line-height:54px;display:block}
.footnote{width:1000px;margin:10px auto 0;text-align:left;font-size:14px;line-height:19px;color:var(--grey);padding-left:190px;padding-right:380px}

/* Press */
.press{height:250px;padding:30px 0 0 110px}
.press-label{font-size:12px;color:var(--grey-dark)}
.press-row{display:flex;gap:34px;align-items:center;margin-top:16px}
.press-row span{display:block;height:34px;background:#b8b8b8}
.press-row.second{margin-top:24px}

/* Footer */
.site-footer{height:335px;background:var(--ink);padding:25px 110px 0;color:var(--footer-text);font-size:12px;line-height:16px;position:relative}
.footer-intro{width:680px}
.group-name{position:absolute;right:110px;top:34px;color:var(--white);font-size:28px;font-weight:600;display:flex;align-items:center;gap:10px}
.group-name i{width:22px;height:22px;border-radius:50%;background:var(--white);display:block}
.site-footer .legal{margin-top:34px}
.site-footer .legal + .legal{margin-top:14px}
.bottom-bar{height:50px;background:var(--grey);color:var(--white);font-size:16px;display:flex;align-items:center;justify-content:center;gap:10px}
.bottom-bar span.circle{width:24px;height:24px;border:2px solid var(--white);border-radius:50%;display:inline-block}
</style>
</head>
<body>

<header class="hero">
  <div class="hero-photo" role="img" aria-label="Photo of a hand holding house keys with a red house-shaped key ring in front of a blurred house"></div>
  <div class="hero-shade"></div>
  <div class="topbar">
    <div class="brand"><span class="brand-dot"></span>pennyduke</div>
    <nav class="main-nav">
      <a href="#">HOME</a><a href="#">SIGN IN</a><a href="#">HOW IT WORKS</a><a href="#">DISCOVER A PROJECT</a><a href="#">THE BARON BLOG</a><a href="#">FIND OUT MORE</a>
    </nav>
    <div class="social"><span></span><span></span></div>
  </div>
  <div class="hero-copy">
    <p class="lead">PROPERTY BUYING</p>
    <h1>IS STRESSFUL, OUTDATED AND IN NEED OF CHANGE.</h1>
  </div>
  <div class="scroll-btn">
    <svg width="36" height="22" viewBox="0 0 36 22"><polyline points="3,3 18,18 33,3" fill="none" stroke="#fff" stroke-width="4"/></svg>
  </div>
  <div class="slider-dots"><span class="active"></span><span></span><span></span></div>
</header>

<section class="intro">
  <div class="intro-icon">
    <svg width="40" height="40" viewBox="0 0 40 40" fill="none" stroke="#fff" stroke-width="4" stroke-linecap="round"><line x1="8" y1="8" x2="32" y2="32"/><line x1="32" y1="8" x2="8" y2="32"/></svg>
  </div>
  <h2>Reconstructing a property ladder that's strong and fair</h2>
  <p>By harnessing the power of crowds, it's possible to become a landlord in locations around the world. Forget the burden of financing 100% of the purchase. Leave the day to day management of your property portfolio to us. Start with 1% in a project and plan your steps to becoming a true baron.</p>
</section>

<section class="actions">
  <div class="action">
    <div class="action-tile">
      <svg width="40" height="40" viewBox="0 0 40 40" fill="none" stroke="#fff" stroke-width="3"><polyline points="16,10 26,20 16,30"/></svg>
      Sign up<br>to buy
    </div>
    <div><h3>Find properties</h3><p>Sign up to browse the portfolio. Your journey to becoming a real estate baron starts here.</p></div>
  </div>
  <div class="action">
    <div class="action-tile">
      <svg width="40" height="40" viewBox="0 0 40 40" fill="none" stroke="#fff" stroke-width="3"><polyline points="16,10 26,20 16,30"/></svg>
      Submit<br>a property
    </div>
    <div><h3>Find buyer</h3><p>Submit a property or development and raise funds from our real estate barons.</p></div>
  </div>
</section>

<section class="projects">
  <h2 class="section-title">Featured Projects</h2>
  <p class="section-sub">Brief details of new and popular projects. To view full listings, you will be required to sign up and <a href="#">become a member</a>.</p>
  <div class="cards">
    <article class="card">
      <div class="card-photo" role="img" aria-label="Photo of a riverside apartment development"></div>
      <span class="tag-new">new launch</span><span class="tag-price">From GBP 3,600</span>
      <div class="card-body">
        <h4>14 Quayside Row LONDON E2</h4>
        <p>A landmark development offering panoramic views across the river Thames less than 2 miles from the City and Canary Wharf.</p>
        <div class="progress"><i style="width:0%"></i></div>
        <div class="funded">0% funded</div>
        <a class="card-link" href="#">See Project Details</a>
      </div>
    </article>
    <article class="card">
      <div class="card-photo" role="img" aria-label="Photo of a residential tower lit at night"></div>
      <span class="tag-new">new launch</span><span class="tag-price">From GBP 3,275</span>
      <div class="card-body">
        <h4>Halden Tower, LONDON E14</h4>
        <p>At the heart of Northgate Wharf, a premium residential project by award winning developer Ferncastle.</p>
        <div class="progress"><i style="width:4%"></i></div>
        <div class="funded">4% funded</div>
        <a class="card-link" href="#">See Project Details</a>
      </div>
    </article>
    <article class="card">
      <div class="card-photo" role="img" aria-label="Photo of a new island apartment quarter by the water"></div>
      <span class="tag-new">new launch</span><span class="tag-price">From GBP 760</span>
      <div class="card-body">
        <h4>Riverbend Isle E14</h4>
        <p>A new island for London, introducing London's most connected location from the multi-award winning developer, Ferncastle Group.</p>
        <div class="progress"><i style="width:51%"></i></div>
        <div class="funded">51% funded</div>
        <a class="card-link" href="#">See Project Details</a>
      </div>
    </article>
  </div>
</section>

<section class="community">
  <h2 class="section-title">Be Part of a Growing International Community</h2>
  <p class="section-sub">Gain access to new projects in world class cities and join our growing community of international landlords.</p>
  <div class="bar-title first">A community of international property &amp; real estate in the maps</div>
  <div class="world-map" role="img" aria-label="World map marking property barons and properties around the globe"></div>
  <div class="legend">
    <div class="legend-row"><i></i>A community of international property barons</div>
    <div class="legend-row"><i class="pink"></i>Attractive real estate from around the world</div>
  </div>
  <div class="bar-title second">Collective buying power of the pennyduke community</div>
  <div class="donut-wrap">
    <svg width="340" height="340" viewBox="0 0 340 340">
      <circle cx="170" cy="170" r="144" fill="none" stroke="var(--green)" stroke-width="52"/>
      <circle cx="170" cy="170" r="144" fill="none" stroke="var(--grey)" stroke-width="52" stroke-dasharray="143 762" transform="rotate(-146.9 170 170)"/>
    </svg>
    <div class="donut-center"><span class="cur">* USD</span><span class="amt">$2.06m</span></div>
    <div class="donut-label invested">Invested 15.8%</div>
    <div class="donut-label pledged">Pledged 84.2%</div>
  </div>
  <p class="footnote">* Graphic shows the combined USD$ amount invested in projects and pledged from aspiring pennydukes</p>
</section>

<section class="press">
  <p class="press-label">Featured in</p>
  <div class="press-row">
    <span style="width:110px"></span><span style="width:110px"></span><span style="width:125px"></span><span style="width:70px"></span><span style="width:45px"></span><span style="width:110px"></span>
  </div>
  <div class="press-row second">
    <span style="width:60px;height:40px"></span><span style="width:110px"></span><span style="width:340px"></span>
  </div>
</section>

<footer class="site-footer">
  <p class="footer-intro">Pennyduke is part of the Sprout Capital Group. Sprout Capital is a worldwide pioneer and leader in the crowd investing, peer to peer and online investment market.</p>
  <div class="group-name"><i></i>Sprout Capital</div>
  <p class="legal">By accessing this site and any pages thereof, you agree to be bound by the terms and conditions. This website is only suitable, intended and available for professional or sophisticated, or similar investors in other jurisdictions, or those who are members of the pennyduke community and familiar with, and willing to accept the risks associated with private participation. Pennyduke does not endorse any of the projects that appear on this website, nor does it make any recommendations regarding the appropriateness of particular opportunities for any participant. Each potential participant must review and evaluate the projects in his or her own discretion and determine the suitability of participating.</p>
  <p class="legal">This website (the "Site") is in every respect unaffiliated with any site to which it links or to any company or entity (and connected projects, investment opportunity or similar) featured on this Site, and is not meant as an endorsement of any of those companies or entities ("third parties"). Furthermore and for the avoidance of doubt, Pennyduke Limited is in no way affiliated with any third parties featured or referenced on this Site. If you believe any content infringes your rights, please refer to our Terms of Service and let us know how to request its removal from the Site.</p>
</footer>
<div class="bottom-bar">© pennyduke 2014 | Follow Pennyduke on <span class="circle"></span><span class="circle"></span></div>

</body>
</html>
```